Business Cards for a law firm

Business cards for our law firm. Use our silhoette logo and OAK PARTNERS - check our website (www.oakpartners.example)

Contact Information for Business Card

our silhouette logo, OAK PARTNERS, 800-555-0147, Dorian Pemberton, dorian@oakpartners.example

Requirements
Must have
• our silhouette logo, OAK PARTNERS, 800-555-0147, Dorian Pemberton, dorian@oakpartners.example

```html
<!DOCTYPE html>
<html lang="en">
<head>
<meta charset="utf-8">
<title>Oak Partners – Business Card</title>
<link href="https://fonts.googleapis.com/css2?family=Krona+One&family=Poppins:wght@400;500&display=swap" rel="stylesheet">
<style>
  :root {
    --canvas: #e4e4e4;
    --paper: #ffffff;
    --royal: #00159e;
    --navy: #00287a;
    --red: #c60000;
    --ink: #0c1424;
  }
  html, body {
    margin: 0;
    width: 1200px;
    height: 1200px;
    overflow: hidden;
    background: var(--canvas);
  }
  .card {
    position: absolute;
    left: 255px;
    width: 788px;
    height: 450px;
    display: block;
  }
  .card--front { top: 129px; }
  .card--back { top: 621px; }
  .holder-name {
    font-family: "Poppins", sans-serif;
    font-weight: 500;
    font-size: 35px;
    fill: var(--red);
  }
  .contact-line {
    font-family: "Poppins", sans-serif;
    font-weight: 400;
    font-size: 19px;
    fill: var(--ink);
  }
  .firm-name {
    font-family: "Krona One", sans-serif;
    font-weight: 400;
  }
  .firm-name--panel { font-size: 17px; fill: var(--paper); }
  .firm-name--feature { font-size: 30px; fill: var(--royal); }
  .icon-ring { fill: none; stroke: var(--ink); stroke-width: 1.6; }
  .icon-glyph { fill: var(--ink); }
  .icon-stroke { fill: none; stroke: var(--ink); stroke-width: 1.4; }
</style>
</head>
<body>

<!-- Front: contact details -->
<svg class="card card--front" viewBox="0 0 788 450" aria-label="Business card front">
  <rect class="paper" width="788" height="450" fill="var(--paper)"/>
  <rect class="accent-band" x="0" y="381" width="520" height="38" fill="var(--red)"/>
  <g class="accent-slashes" fill="var(--royal)">
    <polygon points="283,369 324,369 288,431 246,431"/>
    <polygon points="348,372 384,372 352,427 315,427"/>
    <polygon points="403,375 437,375 408,425 374,425"/>
  </g>
  <path class="side-curve" d="M544,0 L544,450 L543,450 A65,80 0 0 1 478,370 L478,80 A65,80 0 0 1 543,0 Z" fill="var(--navy)"/>
  <rect class="side-panel" x="544" y="0" width="244" height="450" fill="var(--royal)"/>
  <text class="firm-name firm-name--panel" x="661" y="289" text-anchor="middle">OAK PARTNERS</text>

  <g class="holder">
    <g class="icon-person icon-glyph">
      <circle cx="39" cy="132" r="9"/>
      <ellipse cx="39" cy="151" rx="14" ry="7.5"/>
    </g>
    <text class="holder-name" x="63" y="156">Dorian Pemberton</text>
  </g>

  <g class="contacts">
    <g class="contact contact--phone">
      <circle class="icon-ring" cx="39" cy="240" r="12.5"/>
      <path class="icon-glyph" d="M33.5,234.5 c1.5,-1.5 3,-1 3.8,0.6 l1,2 c0.4,0.9 0,1.6 -0.8,2.2 c0.8,1.9 2.2,3.4 4.1,4.2 c0.6,-0.8 1.3,-1.2 2.2,-0.8 l2,1 c1.6,0.8 2,2.3 0.6,3.8 c-1.4,1.3 -3.5,1.2 -5.6,0.1 c-3.2,-1.7 -5.7,-4.3 -7.3,-7.5 c-1,-2 -1.2,-4.2 0,-5.6 z"/>
      <text class="contact-line" x="63" y="247">800-555-0147</text>
    </g>
    <g class="contact contact--email">
      <circle class="icon-ring" cx="39" cy="273" r="12.5"/>
      <rect class="icon-glyph" x="31" y="267.5" width="16" height="11" rx="1.5"/>
      <path d="M32,268.5 L39,274 L46,268.5" fill="none" stroke="var(--paper)" stroke-width="1.4"/>
      <text class="contact-line" x="63" y="280">dorian@oakpartners.example</text>
    </g>
    <g class="contact contact--web">
      <circle class="icon-ring" cx="39" cy="306" r="12.5"/>
      <circle class="icon-stroke" cx="39" cy="306" r="7.5"/>
      <ellipse class="icon-stroke" cx="39" cy="306" rx="3.2" ry="7.5"/>
      <line class="icon-stroke" x1="31.5" y1="306" x2="46.5" y2="306"/>
      <line class="icon-stroke" x1="32.5" y1="302" x2="45.5" y2="302"/>
      <line class="icon-stroke" x1="32.5" y1="310" x2="45.5" y2="310"/>
      <text class="contact-line" x="63" y="313">www.oakpartners.example</text>
    </g>
    <g class="contact contact--address">
      <circle class="icon-ring" cx="39" cy="339" r="12.5"/>
      <path class="icon-glyph" d="M39,348 C35,343 33,339.5 33,336.5 A6,6 0 0 1 45,336.5 C45,339.5 43,343 39,348 Z"/>
      <circle cx="39" cy="336.5" r="2.2" fill="var(--paper)"/>
      <text class="contact-line" x="63" y="346">Your Street,City,State,Pin Code,Country</text>
    </g>
  </g>
</svg>

<!-- Back: firm name -->
<svg class="card card--back" viewBox="0 0 788 450" aria-label="Business card back">
  <rect class="paper" width="788" height="450" fill="var(--paper)"/>
  <rect class="accent-band" x="220" y="381" width="568" height="38" fill="var(--red)"/>
  <g class="accent-slashes" fill="var(--royal)">
    <polygon points="351,375 385,375 414,425 380,425"/>
    <polygon points="404,373 441,373 474,428 436,428"/>
    <polygon points="464,369 505,369 542,431 500,431"/>
  </g>
  <rect class="side-panel" x="0" y="0" width="176" height="450" fill="var(--royal)"/>
  <path class="side-curve" d="M175,0 L176,0 A68,78 0 0 1 244,78 L244,372 A68,78 0 0 1 176,450 L175,450 Z" fill="var(--navy)"/>
  <text class="firm-name firm-name--feature" x="516" y="230" text-anchor="middle">OAK PARTNERS</text>
</svg>

</body>
</html>
```